Basic business card

use my newly created logo - and the phrases (Lower Cost of Test & Accelarated New Product Introduction) - and my new email domain / ID - use at conferences / tradeshows

Industry/Entity Type

semiconductor

Contact Information for Business Card

Daniel K Forde, Owner, communicate via Logo - Lower COT - Cost of Test, Accelerated NPI - New Product Introduction, phone +1 555 613 0946, Harwick, Oregon, USA, daniel.forde@qal-vub.com

Font styles to use
Sans Serif

Requirements
Nice to have
• re-use my logo created via Pixel Harbor last August (#7315926)

```html
<!DOCTYPE html>
<html lang="en">
<head>
<meta charset="utf-8">
<title>QAL-VUB Business Card</title>
<link rel="stylesheet" href="https://fonts.googleapis.com/css2?family=Open+Sans:wght@400;600;700;800&display=swap">
<style>
  :root {
    --backdrop: #2a2a2e;
    --card: #1f1f23;
    --accent: #f39a1e;
    --brand: #5a6a8c;
    --brand-emboss: #2a2a2f;
    --ink: #ffffff;
  }
  * { margin: 0; padding: 0; box-sizing: border-box; }
  html, body {
    width: 1200px; height: 779px; overflow: hidden;
    background: var(--backdrop);
    font-family: "Open Sans", sans-serif;
  }
  .canvas {
    width: 1200px; height: 779px;
    display: flex; align-items: center; justify-content: center; gap: 50px;
  }
  .card {
    position: relative;
    width: 525px; height: 300px;
    background: var(--card);
    border-bottom: 4px solid var(--accent);
    box-shadow: 0 18px 40px rgba(0,0,0,.45);
    overflow: hidden;
  }
  .card-back {
    display: flex; align-items: center; justify-content: center;
  }
  .brand-name {
    font-weight: 700;
    letter-spacing: 1px;
    white-space: nowrap;
  }
  .card-back .brand-name {
    font-size: 64px;
    color: var(--brand-emboss);
  }
  .card-front .brand-name {
    position: absolute; left: 34px; top: 34px;
    font-size: 40px;
    color: var(--brand);
  }
  .contact {
    position: absolute; left: 34px; bottom: 30px;
    color: var(--ink);
  }
  .person { display: flex; align-items: baseline; gap: 12px; margin-bottom: 10px; white-space: nowrap; }
  .person-name { font-size: 32px; font-weight: 800; color: var(--accent); }
  .person-role { font-size: 16px; font-weight: 700; }
  .detail-row { display: flex; gap: 22px; font-size: 13.5px; line-height: 1.7; white-space: nowrap; }
  .label { color: var(--accent); font-weight: 600; margin-right: 4px; }
</style>
</head>
<body>
  <main class="canvas">
    <section class="card card-back">
      <span class="brand-name">QAL-VUB</span>
    </section>
    <section class="card card-front">
      <span class="brand-name">QAL-VUB</span>
      <div class="contact">
        <div class="person">
          <span class="person-name">Daniel K Forde</span>
          <span class="person-role">Owner</span>
        </div>
        <div class="detail-row">
          <span><span class="label">T:</span>555-613-0946</span>
          <span><span class="label">E:</span>daniel.forde@qal-vub.com</span>
        </div>
        <div class="detail-row">
          <span>Harwick, Oregon, USA</span>
          <span><span class="label">W:</span>www.qal-vub.com</span>
        </div>
      </div>
    </section>
  </main>
</body>
</html>
```